Alaska Law Firm Needs a Sticker Design

We need a design for stickers to put on already-printed brochures. We mail the brochures to potential clients so they can learn more about accident-induced injuries, insurance claims, legal representation, and our own law firm.

One of our lawyers wrote a book that provides a helpful overview of personal injury claims. We are offering this book for free to anyone who calls and requests it. Therefore, the sticker design should include one of the following phrases, or something very similar:
a) "Still have questions? Call and request our book-- for free!"
b) "Still have questions about auto accident claims? Call and request our book today."
c) "Still have questions about filing a claim? Call and request a free copy of our book."
d) "Still have questions? Call us today to request a free copy of our book, Clear Lanes Ahead."
e) "To learn more about automobile accidents and insurance, call today and request a free copy of our book."

The sticker should be approximately 3"x3" and may be a circle, square, rectangle, or ellipsis. The sticker will be placed on the back of the folder, which is light blue. We would like the sticker to match the color scheme of our website and the folder.

I will upload an image of the book cover as soon as I obtain it.

Law Firm

Font styles to use
Serif
Sans Serif

Requirements
Should not have
• Bright colors that aren't already used in the folder design. e.g. no bright orange, pink, chartreuse, turquoise, yellow, red.

```html
<!DOCTYPE html>
<html lang="en">
<head>
<meta charset="utf-8">
<title>Free Book Sticker</title>
<link href="https://fonts.googleapis.com/css2?family=Bebas+Neue&family=Roboto:wght@400&family=Open+Sans:wght@400;800&display=swap" rel="stylesheet">
<style>
  :root {
    --navy: #153f68;
    --white: #ffffff;
    --backdrop: #e6e7e8;
    --photo-sky: #dfe9ee;
    --photo-green: #5f9a3c;
  }
  * { margin: 0; padding: 0; box-sizing: border-box; }
  html, body { width: 1200px; height: 855px; overflow: hidden; }
  body { background: var(--backdrop); position: relative; }

  .sticker {
    position: absolute; left: 264px; top: 108px;
    width: 672px; height: 672px; border-radius: 50%;
    background: var(--white); overflow: hidden;
    box-shadow: 0 3px 10px rgba(0,0,0,0.18);
  }
  .headline {
    position: absolute; top: 80px; left: 0; width: 100%;
    text-align: center; font-family: "Bebas Neue", sans-serif;
    font-size: 127px; line-height: 1; color: var(--navy);
  }
  .question-band {
    position: absolute; top: 220px; left: 10px; width: 654px; height: 90px;
    background: var(--navy); display: flex; align-items: center;
  }
  .question-band span {
    margin-left: 44px; font-family: "Bebas Neue", sans-serif;
    font-size: 74px; line-height: 1; letter-spacing: 8px; color: var(--white);
    padding-top: 6px;
  }
  .call-line {
    position: absolute; top: 342px; left: 69px;
    font-family: "Bebas Neue", sans-serif; font-size: 43px; line-height: 1;
    color: var(--navy); white-space: nowrap;
  }
  .phone {
    position: absolute; top: 386px; left: 68px;
    font-family: "Roboto", sans-serif; font-size: 48px; line-height: 1;
    color: var(--navy); white-space: nowrap;
  }
  .free-band {
    position: absolute; top: 478px; left: 0; width: 100%; height: 200px;
    background: var(--navy);
  }
  .free-band span {
    position: absolute; top: 4px; left: 0; width: 100%; text-align: center;
    font-family: "Bebas Neue", sans-serif; font-size: 152px; line-height: 1;
    color: var(--white);
  }

  .book {
    position: absolute; left: 436px; top: 212px; width: 188px; height: 304px;
    background: var(--white); display: flex; flex-direction: column;
    box-shadow: 4px 4px 8px rgba(0,0,0,0.3); border: 1px solid #d5d9dd;
  }
  .book-author {
    margin-top: 14px; text-align: center; font-family: "Open Sans", sans-serif;
    font-size: 12px; color: var(--navy); letter-spacing: -0.2px;
  }
  .book-title {
    margin-top: 6px; text-align: center; font-family: "Open Sans", sans-serif;
    font-weight: 800; font-size: 21px; line-height: 1.02; color: var(--navy);
  }
  .book-photo {
    flex: 1; margin-top: 8px;
    background: linear-gradient(180deg, var(--photo-sky) 0%, #a9c79a 40%, var(--photo-green) 100%);
  }
  .book-strip {
    height: 34px; background: var(--navy); color: var(--white);
    font-family: "Open Sans", sans-serif; font-size: 8px; line-height: 1.3;
    text-align: center; text-transform: uppercase; padding-top: 6px;
  }
</style>
</head>
<body>
  <div class="sticker">
    <div class="headline">Still Have</div>
    <div class="question-band"><span>Questions?</span></div>
    <div class="call-line">Call &amp; Request Our Book</div>
    <div class="phone">(907) 555-0148</div>
    <div class="free-band"><span>FREE !!</span></div>

    <div class="book">
      <div class="book-author">DANIEL R. HARTLEY</div>
      <div class="book-title">CLEAR LANES<br>AHEAD</div>
      <div class="book-photo" role="img" aria-label="Cover photo of a smiling family lying on the grass outdoors with a small red car"></div>
      <div class="book-strip">The right way to handle<br>your auto accident claim</div>
    </div>
  </div>
</body>
</html>
```